SOLVE Study flyer

I need help designing a flyer for a research study that will include brain imaging in adolescents. The info is in the attached document. The study is called the Sequoia Outlook Lantern Valley Echo (SOLVE) study. Ideally this would be returned as a document that I can edit in the future as we will have several new recruitment phases (different age groups, etc. I also would love to have a logo designed as part of this project, but I recognize that might be a separate design request.

```html
<!DOCTYPE html>
<html lang="en">
<head>
<meta charset="utf-8">
<title>SOLVE Study Recruitment Flyer</title>
<link rel="stylesheet" href="https://fonts.googleapis.com/css2?family=Montserrat:wght@500;600;700;800&family=Lato:wght@400;700&display=swap">
<style>
  :root {
    --navy: #0c1d4b;
    --navy-deep: #091638;
    --cyan: #1fd3df;
    --teal: #169aa0;
    --panel: #e6f3f4;
    --ink: #3b4653;
    --white: #ffffff;
  }
  * { box-sizing: border-box; margin: 0; padding: 0; }
  html, body { width: 927px; height: 1200px; overflow: hidden; background: var(--white); }
  .flyer { position: relative; width: 927px; height: 1200px; overflow: hidden; font-family: "Lato", sans-serif; color: var(--ink); }
  .backdrop { position: absolute; inset: 0; width: 927px; height: 1200px; }
  .headline { position: absolute; left: 34px; top: 40px; font-family: "Montserrat", sans-serif; font-weight: 800; color: var(--white); font-size: 38.5px; line-height: 43px; letter-spacing: 0.3px; }
  .headline-age { position: absolute; left: 31px; top: 130px; font-family: "Montserrat", sans-serif; font-weight: 800; color: var(--cyan); font-size: 76px; line-height: 80px; letter-spacing: -2px; }
  .subhead { position: absolute; left: 33px; top: 213px; font-family: "Montserrat", sans-serif; font-weight: 500; color: var(--white); font-size: 27px; line-height: 32px; }
  .intro { position: absolute; left: 34px; top: 293px; width: 410px; color: var(--white); font-size: 17px; line-height: 22px; }
  .age-badge { position: absolute; left: 296px; top: 383px; width: 166px; height: 166px; border-radius: 50%; background: var(--navy); border: 3px solid var(--white); text-align: center; font-family: "Montserrat", sans-serif; }
  .age-badge-label { margin-top: 46px; color: var(--white); font-weight: 600; font-size: 19px; line-height: 22px; }
  .age-badge-range { color: var(--teal); font-weight: 700; font-size: 52px; line-height: 56px; letter-spacing: -1px; }
  .section-title { position: absolute; font-family: "Montserrat", sans-serif; font-weight: 600; color: var(--navy); font-size: 25.5px; line-height: 29px; }
  .section-rule { position: absolute; height: 3px; width: 89px; background: var(--teal); border-radius: 2px; }
  .bullet-list { position: absolute; list-style: none; font-size: 16.3px; line-height: 23.5px; }
  .bullet-list li { position: relative; padding-left: 19px; margin-bottom: 11px; }
  .bullet-list li::before { content: ""; position: absolute; left: 0; top: 7px; width: 9px; height: 9px; border-radius: 50%; background: var(--teal); }
  .participation { left: 35px; top: 700px; width: 363px; text-align: justify; }
  .eligibility { left: 508px; top: 805px; width: 365px; }
  .eligibility li { margin-bottom: 17px; text-align: justify; }
  .contact { position: absolute; left: 500px; display: flex; align-items: center; }
  .contact-icon { width: 56px; height: 56px; border-radius: 50%; background: var(--navy); display: flex; align-items: center; justify-content: center; }
  .contact-text { margin-left: 17px; }
  .contact-label { font-family: "Montserrat", sans-serif; font-weight: 600; color: var(--navy); font-size: 18.5px; line-height: 22px; }
  .contact-value { font-size: 17px; line-height: 22px; color: var(--ink); }
  .contact-amount { font-family: "Montserrat", sans-serif; font-weight: 700; color: var(--teal); font-size: 26px; }
</style>
</head>
<body>
<main class="flyer">
  <svg class="backdrop" viewBox="0 0 927 1200" aria-hidden="false">
    <defs>
      <linearGradient id="swing-tones" x1="0" y1="0" x2="1" y2="1">
        <stop offset="0" stop-color="#8fb0d6"/>
        <stop offset="0.5" stop-color="#b88a6c"/>
        <stop offset="1" stop-color="#6e7f4a"/>
      </linearGradient>
      <linearGradient id="group-tones" x1="0" y1="0" x2="0" y2="1">
        <stop offset="0" stop-color="#9aa0a6"/>
        <stop offset="0.55" stop-color="#a9a3c4"/>
        <stop offset="1" stop-color="#5f7491"/>
      </linearGradient>
      <linearGradient id="friends-tones" x1="0" y1="0" x2="1" y2="0">
        <stop offset="0" stop-color="#d9b79a"/>
        <stop offset="0.45" stop-color="#a35b8c"/>
        <stop offset="1" stop-color="#9fb6d3"/>
      </linearGradient>
      <linearGradient id="navy-shade" x1="0" y1="0" x2="0" y2="1">
        <stop offset="0" stop-color="#0c1d4b"/>
        <stop offset="1" stop-color="#11265a"/>
      </linearGradient>
    </defs>

    <rect class="panel-light" x="460" y="560" width="467" height="640" fill="var(--panel)"/>

    <path class="hero-navy" role="img" aria-label="Dim backdrop photo of a parent and daughter" d="M0 0 H927 V640 C830 655 700 650 600 610 L460 600 V520 H0 Z" fill="url(#navy-shade)"/>
    <path class="hero-wave-right" d="M600 610 C700 660 820 665 927 628 V640 C830 680 700 672 630 640 Z" fill="var(--teal)"/>

    <path class="hero-wave-left" d="M0 500 C120 505 190 495 240 455 C270 432 300 428 330 428 L330 560 L0 560 Z" fill="var(--teal)"/>
    <path class="hero-white-left" d="M0 548 C110 548 175 540 210 515 C250 488 290 470 330 468 L460 468 V560 H0 Z" fill="var(--white)"/>

    <circle cx="733" cy="242" r="240" fill="var(--white)"/>
    <circle class="photo-swing" role="img" aria-label="Photo of a girl on a playground swing against the sky" cx="733" cy="242" r="226" fill="url(#swing-tones)"/>

    <circle cx="571" cy="508" r="143" fill="var(--white)"/>
    <circle class="photo-group" role="img" aria-label="Photo of four smiling schoolgirls with backpacks" cx="571" cy="508" r="133" fill="url(#group-tones)"/>

    <rect class="photo-friends" role="img" aria-label="Photo of four girls laughing and chatting together" x="0" y="895" width="460" height="250" fill="url(#friends-tones)"/>

    <path class="footer-teal" d="M0 1100 C200 1095 380 1150 560 1150 C720 1150 850 1110 927 1050 V1200 H0 Z" fill="var(--teal)"/>
    <path class="footer-navy" d="M0 1125 C180 1105 380 1140 540 1170 C700 1200 830 1160 927 1108 V1200 H0 Z" fill="var(--navy)"/>
  </svg>

  <h1 class="headline">ARE YOU THE PARENT<br>OF A CHILD AGE</h1>
  <div class="headline-age">10-17?</div>
  <p class="subhead">Do they worry or overthink<br>negative emotions?</p>
  <p class="intro">Harborview Institute researchers are seeking girls age 10-17 for a study about brain activity in emotions and decision-making and how they relate to puberty, anxiety and depression.</p>

  <div class="age-badge">
    <div class="age-badge-label">Are Age</div>
    <div class="age-badge-range">10-17</div>
  </div>

  <h2 class="section-title" style="left:35px; top:627px;">Study Participation Involves:</h2>
  <div class="section-rule" style="left:36px; top:666px;"></div>
  <ul class="bullet-list participation">
    <li>One one-hour interview (online or in-person) where your child will discuss their thoughts</li>
    <li>Online questionnaires (parent and child)</li>
    <li>One two-hour visit where your child will complete an MRI scan, answer questions about their puberty stage, and have a small hair sample taken to study puberty hormones</li>
  </ul>

  <h2 class="section-title" style="left:509px; top:708px;">Your Child May be Eligible<br>&nbsp;if they:</h2>
  <div class="section-rule" style="left:509px; top:777px;"></div>
  <ul class="bullet-list eligibility">
    <li>Are age 10-17</li>
    <li>Tend to worry or overthink negative thoughts</li>
    <li>have not been diagnosed with psychosis, learning problems, or autism Interested in participating? Want more information? Please contact us!</li>
  </ul>

  <div class="contact" style="top:988px;">
    <div class="contact-icon">
      <svg width="24" height="18" viewBox="0 0 24 18" aria-hidden="true">
        <rect x="0" y="0" width="24" height="18" rx="2" fill="var(--white)"/>
        <path d="M1 2 L12 10 L23 2" fill="none" stroke="var(--navy)" stroke-width="2"/>
      </svg>
    </div>
    <div class="contact-text">
      <div class="contact-label">Email</div>
      <div class="contact-value">solvestudy@harborview-research.org</div>
    </div>
  </div>

  <div class="contact" style="top:1064px;">
    <div class="contact-icon">
      <svg width="26" height="26" viewBox="0 0 26 26" aria-hidden="true">
        <rect x="1" y="8" width="24" height="6" rx="1" fill="var(--white)"/>
        <rect x="3" y="15" width="20" height="10" rx="1" fill="var(--white)"/>
        <rect x="12" y="8" width="2" height="17" fill="var(--navy)"/>
        <path d="M13 8 C10 2 5 3 7 7 Z M13 8 C16 2 21 3 19 7 Z" fill="var(--white)"/>
      </svg>
    </div>
    <div class="contact-text">
      <div class="contact-label">Compensation</div>
      <div class="contact-value">up to <span class="contact-amount">$140</span></div>
    </div>
  </div>
</main>
</body>
</html>
```